ASSET BASED PROGRAM FLIER

Need flier to market hard money loan products offered HARD MONEY FIX & FLIP PROGRAMS

We offer a variety of loan programs Some program highlights include......

1) No Minimum Credit Score
2) 3-5 Day Close
3) Up to 100% of Purchase & Rehab
4) Rates as Low as 7%
5) Loans Offered Nationwide

Contact us today for more information at (800) 416-9052 x23 or email us at mbelcourt@quillmarkfunding.com NMLS #318746 www.quillmarkfunding.com

Industry/Entity Type

Loan

```html
<!DOCTYPE html>
<html lang="en">
<head>
<meta charset="utf-8">
<title>Hard Money Fix &amp; Flip Programs – Quillmark Funding</title>
<link rel="stylesheet" href="https://fonts.googleapis.com/css2?family=Cinzel:wght@600;700&family=Roboto:ital,wght@0,400;0,500;0,700;1,500&display=swap">
<style>
  :root {
    --blue: #0b5fa8;
    --blue-mid: #1a7fd0;
    --blue-bright: #08a3e3;
    --gold: #b2a15c;
    --gold-dark: #8f7f3c;
    --charcoal: #2f2f31;
    --ink: #1d1d1d;
    --navy: #0d2a55;
    --white: #ffffff;
    --wall: #e4e4e4;
  }
  * { box-sizing: border-box; margin: 0; padding: 0; }
  html, body { width: 1200px; height: 1200px; overflow: hidden; background: var(--wall); }
  .flier {
    position: absolute; left: 176px; top: 0;
    width: 848px; height: 1200px;
    background: var(--white);
    font-family: "Roboto", sans-serif;
    color: var(--ink);
    overflow: hidden;
  }
  .header-shapes { position: absolute; left: 0; top: 0; }
  .brand {
    position: absolute; left: 492px; top: 122px;
    display: flex; align-items: center; gap: 8px;
  }
  .brand-dot { width: 22px; height: 22px; border-radius: 50%; background: var(--gold); }
  .brand-name {
    font-family: "Cinzel", serif; font-weight: 700; font-size: 17px;
    color: var(--gold-dark); white-space: nowrap;
  }
  .hero-photo {
    position: absolute; left: 32px; top: 176px; width: 816px; height: 381px;
    background: linear-gradient(100deg, #3f8a4e 0%, #d9d1c4 22%, #f2efe9 50%, #e8e3da 72%, #c9a782 100%);
  }
  .headline {
    position: absolute; left: 80px; top: 578px;
    font-family: "Cinzel", serif; font-weight: 700; line-height: 1;
  }
  .headline .line-1 { display: block; color: var(--blue); font-size: 61px; letter-spacing: 1px; }
  .headline .line-2 { display: block; color: var(--gold); font-size: 76px; margin-top: 6px; letter-spacing: 1px; }
  .about {
    position: absolute; left: 78px; top: 748px; width: 384px;
    font-size: 17px; line-height: 21.3px; text-align: justify;
  }
  .programs-head {
    position: absolute; left: 493px; top: 740px; width: 355px; height: 110px;
    background: linear-gradient(180deg, #3a3a3c, #4a4a4c);
    border-top: 8px solid var(--gold);
    padding: 18px 0 0 12px;
    font-size: 23px; line-height: 29px; text-transform: uppercase;
  }
  .programs-head .lead { color: var(--white); display: block; }
  .programs-head .accent {
    color: var(--gold); font-weight: 500; display: inline-block;
    border-bottom: 2px solid var(--gold); padding-bottom: 2px;
  }
  .program-list { position: absolute; left: 502px; top: 856px; list-style: none; }
  .program-list li {
    display: flex; align-items: center; gap: 16px;
    font-weight: 700; font-size: 18px; line-height: 22px; color: var(--ink);
  }
  .program-list li + li { margin-top: 10px; }
  .program-list li.tall { margin-top: 14px; margin-bottom: 6px; }
  .icon {
    flex: none; width: 36px; height: 36px; border-radius: 50%;
    background: var(--gold); box-shadow: 2px 3px 3px rgba(0,0,0,.3);
    display: flex; align-items: center; justify-content: center;
  }
  .icon svg { width: 20px; height: 20px; }
  .makeover {
    position: absolute; left: 0; top: 880px; width: 466px; height: 224px;
    background: var(--gold);
  }
  .makeover .shot {
    position: absolute; top: 12px; width: 204px; height: 176px;
    border: 3px solid #1c1c1c;
  }
  .shot.before { left: 14px; background: linear-gradient(160deg, #c88a4a, #e8d8c0 55%, #a86a35); }
  .shot.after { left: 225px; background: linear-gradient(160deg, #3a2418, #7a5a3a 55%, #2a1a12); }
  .makeover .label {
    position: absolute; top: 190px; width: 204px; text-align: center;
    font-family: "Cinzel", serif; font-weight: 700; font-size: 18px; color: var(--white);
  }
  .label.before { left: 14px; }
  .label.after { left: 225px; }
  .contact-bar {
    position: absolute; left: 0; top: 1125px; width: 848px; height: 75px;
    background: var(--blue); color: var(--white);
    text-align: center; font-size: 16px; line-height: 20px; padding-top: 7px;
  }
  .contact-bar em { font-style: italic; font-weight: 500; color: var(--navy); }
</style>
</head>
<body>
<main class="flier">
  <svg class="header-shapes" width="848" height="600" viewBox="0 0 848 600" aria-hidden="true">
    <rect x="0" y="0" width="848" height="176" fill="var(--blue)"/>
    <polygon points="0,0 430,0 250,176 0,176" fill="#0a57a0"/>
    <polygon points="595,0 848,0 848,176" fill="var(--blue-mid)"/>
    <polygon points="700,0 848,0 848,60 760,110" fill="var(--blue)"/>
    <polygon points="740,110 848,20 848,176" fill="var(--blue-bright)"/>
    <polygon points="425,176 595,0 848,176" fill="var(--white)"/>
    <polygon points="0,176 32,176 32,540 0,590" fill="var(--blue)"/>
  </svg>

  <div class="brand">
    <span class="brand-dot"></span>
    <span class="brand-name">Quillmark Funding, Inc.</span>
  </div>

  <div class="hero-photo" role="img" aria-label="Photo of a businesswoman and a contractor in a hard hat reviewing a clipboard in a bright renovated kitchen with a ladder and plants"></div>

  <h1 class="headline">
    <span class="line-1">HARD MONEY FIX &amp;</span>
    <span class="line-2">FLIP PROGRAMS</span>
  </h1>

  <p class="about">Quillmark Funding, Inc. was established in August 1997 by Marcel Belcourt. Over the years we have grown from a basement operated “one man show” to a staff of over 70 just before the real estate decline which started in 2007.</p>

  <div class="programs-head">
    <span class="lead">We offer a variety of</span>
    <span class="accent">Loan Programs</span>
  </div>

  <ul class="program-list">
    <li><span class="icon"><svg viewBox="0 0 20 20"><circle cx="8" cy="8" r="5" fill="none" stroke="#2a2a2a" stroke-width="2"/><line x1="12" y1="12" x2="17" y2="17" stroke="#2a2a2a" stroke-width="2.5"/></svg></span>No Minimum Credit Score</li>
    <li><span class="icon"><svg viewBox="0 0 20 20"><rect x="3" y="4" width="14" height="13" fill="none" stroke="#2a2a2a" stroke-width="2"/><line x1="3" y1="8" x2="17" y2="8" stroke="#2a2a2a" stroke-width="2"/></svg></span>3-5 Day Close</li>
    <li class="tall"><span class="icon"><svg viewBox="0 0 20 20"><ellipse cx="10" cy="5" rx="6" ry="2.5" fill="#2a2a2a"/><ellipse cx="10" cy="10" rx="6" ry="2.5" fill="#2a2a2a"/><ellipse cx="10" cy="15" rx="6" ry="2.5" fill="#2a2a2a"/></svg></span>Up to 100% of Purchase<br>&amp; Rehab</li>
    <li><span class="icon"><svg viewBox="0 0 20 20"><path d="M2 4h3l2 9h9l2-7H6" fill="none" stroke="#2a2a2a" stroke-width="2"/><circle cx="8" cy="16" r="1.5" fill="#2a2a2a"/><circle cx="15" cy="16" r="1.5" fill="#2a2a2a"/></svg></span>Rates as Low as 7%</li>
    <li><span class="icon"><svg viewBox="0 0 20 20"><path d="M2 10 10 3l8 7M5 8v9h10V8" fill="none" stroke="#2a2a2a" stroke-width="2"/></svg></span>Loans Offered Nationwide</li>
  </ul>

  <section class="makeover">
    <div class="shot before" role="img" aria-label="Before photo of a dated kitchen with light oak cabinets"></div>
    <div class="shot after" role="img" aria-label="After photo of a remodeled kitchen with dark cabinets and pendant lights"></div>
    <span class="label before">BEFORE</span>
    <span class="label after">AFTER</span>
  </section>

  <footer class="contact-bar">
    Contact us today for more information at <em>(800) 416-9052 x23</em> or<br>
    email us at <em>mbelcourt@quillmarkfunding.com</em> NMLS #318746 <em>www.quillmarkfunding.com</em>
  </footer>
</main>
</body>
</html>
```